WEBSITE & LOGO for MEDICAL CILINC

BRAND NAME ( LUMORA) Medical clinic for intravenous (IV) vitamin hydration and wellness therapy. range of signature infusions and boosters are targeted at preventative health and wellness – essentially replenishing your body with the fluids and vitamins it needs to be in tip-top condition.

Blood testing
laboratory analysis
IV therapy
IV infusion drips
phlebotomy services
nurses for Home care services
Patient repatriation services to their countries
Hire of medical equipments including beds and wheel chairs

www.quellsa.com
www.tovexclinic.com
http://pickaflask.co.uk

All adults
18+ women and men.

No black color in the background
DNA double helix image should to be implemented in the design and logo.
the website should be easy to be used so the clients can add to the shopping cart
- select treatment or drips
- supplement
- book nurses
- book home visit
- book nurse for international home care journey

Colors
86cae7
33b8a4
e4daeb
f9d9e8
fefafc
fbd2d3
eee9f4
85acd3
0455a3

Requirements
Must have
• DNA Double helix in Java animation
injection icon for IV injection
Infusion Icon Bag for IV infusion
Analysis icon
phlebotomy services icon
Patient repatriation services icon
Hire of medical equipments icon

light background and water blue menu and buttons with highlights
Nice to have
• dynamic website where
IV injections scroll from side to side
IV infusion scroll from side to side.

```html
<!DOCTYPE html>
<html lang="en">
<head>
<meta charset="utf-8">
<title>Lumora intravenous medical clinic</title>
<link href="https://fonts.googleapis.com/css2?family=Montserrat:ital,wght@0,400;0,500;0,600;1,400&display=swap" rel="stylesheet">
<style>
:root{
  --navy:#0a3f9e;
  --blue:#0455a3;
  --deep:#123f97;
  --teal:#33b8a4;
  --sky:#86cae7;
  --lav:#ebe3f2;
  --lav-soft:#f3eff8;
  --text:#6c7280;
  --white:#ffffff;
  --line:#8f96a6;
}
*{margin:0;padding:0;box-sizing:border-box}
html,body{width:1200px;height:4357px;overflow:hidden}
body{font-family:'Montserrat',sans-serif;background:var(--white);position:relative;color:var(--text)}
.abs{position:absolute}
.ph{position:absolute}
.btn{position:absolute;display:flex;align-items:center;justify-content:center;border-radius:30px;color:#fff;font-weight:600;font-size:15px;background:linear-gradient(90deg,var(--teal),var(--blue));box-shadow:0 6px 14px rgba(4,85,163,.25)}
.eyebrow{position:absolute;left:0;width:1200px;text-align:center;color:var(--teal);font-size:17px;font-weight:500}
.heading{position:absolute;left:0;width:1200px;text-align:center;color:var(--deep);font-size:26px;font-weight:500}

/* hero */
.hero{position:absolute;left:0;top:0;width:1200px;height:558px;background:linear-gradient(120deg,#0b3f97 0%,#0f56b1 55%,#1d6cc4 100%);overflow:hidden}
.brand{position:absolute;display:flex;align-items:center;gap:12px;color:#fff}
.brand-mark{width:30px;height:30px;border-radius:50%;border:2px solid #fff}
.brand-name{font-size:16px;font-weight:600;line-height:1.1}
.brand-sub{font-size:10px;line-height:1.2;font-weight:400}
.nav a{position:absolute;top:36px;color:#fff;font-size:17px;font-weight:500;text-decoration:none}
.nav a.active{color:var(--teal)}
.cart{position:absolute;left:1037px;top:27px;width:48px;height:48px;border-radius:50%;background:var(--teal);border:2px solid #fff}
.cart-badge{position:absolute;left:1066px;top:20px;width:20px;height:20px;border-radius:50%;background:var(--teal);border:1.5px solid #fff;color:#fff;font-size:11px;display:flex;align-items:center;justify-content:center}
.hero-title{position:absolute;left:107px;top:165px;color:#fff;font-size:52px;font-weight:500;line-height:60px;letter-spacing:1px}
.hero-text{position:absolute;left:107px;top:298px;width:520px;color:#fff;font-size:13.5px;line-height:24px}

/* about */
.about-text{position:absolute;left:655px;top:788px;width:445px;font-size:13px;line-height:25.7px;text-align:justify}
.about-link{position:absolute;left:655px;top:1010px;color:var(--teal);font-size:13px;font-weight:600;text-decoration:underline}

/* services */
.services{position:absolute;left:0;top:1147px;width:1200px;height:886px;background:var(--lav)}
.svc-icon{position:absolute;width:74px;height:74px;border-radius:50%;background:linear-gradient(135deg,var(--teal),var(--blue));box-shadow:0 4px 10px rgba(4,85,163,.25)}
.svc-icon svg{width:74px;height:74px}
.svc-label{position:absolute;color:var(--deep);font-size:17px;font-weight:500;white-space:nowrap}
.svc-label.left{text-align:right}

/* testimonials */
.quote{position:absolute;width:400px;text-align:center;font-style:italic;font-size:13px;line-height:26px;color:#8a8f9a}
.person{position:absolute;width:400px;text-align:center;color:var(--deep);font-size:17px;font-weight:500}
.avatar{position:absolute;width:108px;height:108px;border-radius:50%}

/* blog */
.blog{position:absolute;left:0;top:2661px;width:1200px;height:653px;background:var(--lav)}
.card{position:absolute;top:2853px;width:308px;height:368px;background:#fff;box-shadow:0 4px 14px rgba(60,40,100,.08)}
.card-img{position:absolute;left:5px;top:6px;width:298px;height:172px}
.card-meta{position:absolute;left:17px;top:193px;font-size:10.5px;color:#555;word-spacing:2px}
.card-meta span{margin-right:18px}
.card-title{position:absolute;left:17px;top:214px;width:280px;font-size:16.5px;line-height:26px;color:var(--teal);font-weight:500}
.card-body{position:absolute;left:17px;top:275px;width:265px;font-size:12.5px;line-height:26px;color:#7a7f8a}

/* contact */
.field{position:absolute;height:40px;border-bottom:1.5px solid var(--line)}
.field span{position:absolute;left:22px;bottom:4px;font-style:italic;font-size:17px;color:#777}

/* footer */
.footer{position:absolute;left:0;top:3998px;width:1200px;height:359px;background:var(--navy);color:#fff}
.f-head{position:absolute;top:80px;font-size:17px;font-weight:600;letter-spacing:.3px}
.f-list{position:absolute;list-style:none;font-size:15px}
.f-list li{height:25.7px;display:flex;align-items:center;gap:8px}
.f-text{position:absolute;font-size:13px;line-height:26px}
.social{position:absolute;display:flex;align-items:center;gap:16px;font-size:15px}
.social i{width:30px;height:30px;border-radius:50%;background:#1f5bbb;display:block}
.copy{position:absolute;left:0;top:4289px;width:1200px;text-align:center;font-size:12px;color:#fff}
</style>
</head>
<body>

<!-- HERO -->
<section class="hero">
  <div class="ph" style="left:0;top:0;width:1200px;height:558px;background:radial-gradient(ellipse at 80% 20%,rgba(134,202,231,.22),transparent 55%)" role="img" aria-label="Faint DNA double helix pattern across the blue background"></div>
  <div class="brand" style="left:112px;top:22px">
    <div class="brand-mark"></div>
    <div>
      <div class="brand-name">Lumora</div>
      <div class="brand-sub">intravenous<br>medical clinic</div>
    </div>
  </div>
  <nav class="nav">
    <a class="active" style="left:389px">Home</a>
    <a style="left:491px">About Us</a>
    <a style="left:619px">Services</a>
    <a style="left:740px">FAQ</a>
    <a style="left:824px">Blog</a>
    <a style="left:912px">Contact Us</a>
  </nav>
  <div class="cart">
    <svg viewBox="0 0 48 48" width="44" height="44"><path d="M14 17h4l3 12h11l3-9H19" fill="none" stroke="#fff" stroke-width="2.2" stroke-linejoin="round"/><circle cx="22" cy="33" r="1.8" fill="#fff"/><circle cx="31" cy="33" r="1.8" fill="#fff"/></svg>
  </div>
  <div class="cart-badge">2</div>

  <h1 class="hero-title">Lumora&nbsp; intravenous<br>medical clinic</h1>
  <p class="hero-text">Lorem ipsum dolor sit amet, consectetur adipiscing elit, sed do eiusmod tempor incididunt ut labore et dolore magna aliqua.</p>
  <div class="btn" style="left:108px;top:376px;width:149px;height:54px;border:2px solid #fff">Book Nurses</div>

  <div class="ph" style="left:694px;top:70px;width:423px;height:488px;background:linear-gradient(180deg,#7f9ec6 0%,#dfe6ef 55%,#f2f4f7 100%);border-radius:200px 200px 0 0" role="img" aria-label="Smiling senior doctor in a white coat with a stethoscope"></div>

  <svg class="abs" style="left:589px;top:500px" width="22" height="38" viewBox="0 0 22 38"><rect x="2" y="2" width="18" height="34" rx="9" fill="none" stroke="#fff" stroke-width="2"/><line x1="11" y1="8" x2="11" y2="14" stroke="#fff" stroke-width="2" stroke-linecap="round"/></svg>
</section>

<!-- ABOUT -->
<section>
  <div class="ph" style="left:91px;top:652px;width:488px;height:401px;background:linear-gradient(135deg,#c9ccd3 0%,#e8e2dc 50%,#b7a7a8 100%)" role="img" aria-label="Nurse smiling with an elderly woman patient"></div>
  <div class="abs" style="left:655px;top:667px;color:var(--teal);font-size:17px;font-weight:500">About Us</div>
  <h2 class="abs" style="left:655px;top:702px;width:480px;color:var(--deep);font-size:26px;font-weight:500;line-height:36px">Lorem ipsum dolor sit amet conse ctetur adipiscing elit</h2>
  <p class="about-text">Lorem ipsum dolor sit amet, consectetur adipiscing elit, sed do eiusmod tempor incididunt ut labore et dolore magna aliqua. Ut enim ad minim veniam, quis nostrud exercitation ullamco laboris nisi ut aliquip ex ea commodo consequat. Duis aute irure dolor in reprehenderit in voluptate velit esse cillum dolore eu fugiat nulla pariatur. Excepteur sint occaecat cupidatat non proident, sunt in culpa qui officia deserunt mollit anim id est laborum.</p>
  <a class="about-link">book nurse for international home care journey</a>
</section>

<!-- SERVICES -->
<section class="services">
  <div class="ph" style="left:0;top:0;width:1200px;height:886px;background:radial-gradient(ellipse at 90% 20%,rgba(255,255,255,.45),transparent 50%),radial-gradient(ellipse at 10% 80%,rgba(255,255,255,.35),transparent 45%)" role="img" aria-label="Faint molecular and DNA helix pattern"></div>
</section>
<div class="eyebrow" style="top:1237px">Services</div>
<h2 class="heading" style="top:1267px">What We Do</h2>

<svg class="abs" style="left:464px;top:1398px" width="356" height="356"><circle cx="178" cy="178" r="176" fill="none" stroke="#8e93b3" stroke-width="1.5" stroke-dasharray="2 5"/></svg>
<div class="ph" style="left:505px;top:1362px;width:278px;height:486px;background:linear-gradient(180deg,#5b3a32 0%,#e9dfd9 30%,#f6f7fa 60%,#dde3ea 100%);border-radius:130px 130px 0 0" role="img" aria-label="Smiling female doctor in a white coat pointing to the services"></div>

<div class="svc-label left" style="right:842px;top:1419px">laboratory analysis</div>
<div class="svc-icon" style="left:373px;top:1393px"><svg viewBox="0 0 74 74"><g fill="none" stroke="#fff" stroke-width="2"><rect x="32" y="22" width="8" height="16" rx="1"/><path d="M27 50h22M30 50a10 10 0 0 1 12-14"/><line x1="36" y1="18" x2="36" y2="22"/></g></svg></div>

<div class="svc-label left" style="right:842px;top:1573px">Blood testing</div>
<div class="svc-icon" style="left:373px;top:1547px"><svg viewBox="0 0 74 74"><g fill="none" stroke="#fff" stroke-width="2"><rect x="25" y="22" width="10" height="28" rx="5"/><line x1="23" y1="22" x2="37" y2="22"/><path d="M46 28c4 6 7 10 7 14a7 7 0 0 1-14 0c0-4 3-8 7-14z"/></g></svg></div>

<div class="svc-label left" style="right:842px;top:1729px">nurses for Home care services</div>
<div class="svc-icon" style="left:373px;top:1703px"><svg viewBox="0 0 74 74"><g fill="none" stroke="#fff" stroke-width="2"><path d="M28 28h18v-6H28z"/><circle cx="37" cy="34" r="6"/><path d="M25 54c0-8 5-12 12-12s12 4 12 12z"/></g></svg></div>

<div class="svc-icon" style="left:835px;top:1393px"><svg viewBox="0 0 74 74"><g fill="none" stroke="#fff" stroke-width="2"><rect x="24" y="20" width="14" height="20" rx="3"/><path d="M31 40v8a6 6 0 0 0 12 0"/><path d="M48 26c3 5 5 7 5 10a5 5 0 0 1-10 0c0-3 2-5 5-10z"/></g></svg></div>
<div class="svc-label" style="left:922px;top:1419px">IV therapy</div>

<div class="svc-icon" style="left:835px;top:1547px"><svg viewBox="0 0 74 74"><g fill="none" stroke="#fff" stroke-width="2"><rect x="27" y="20" width="20" height="26" rx="4"/><line x1="31" y1="28" x2="43" y2="28"/><line x1="31" y1="34" x2="43" y2="34"/><line x1="37" y1="46" x2="37" y2="56"/></g></svg></div>
<div class="svc-label" style="left:922px;top:1573px">IV infusion drips</div>

<div class="svc-icon" style="left:835px;top:1703px"><svg viewBox="0 0 74 74"><g fill="none" stroke="#fff" stroke-width="2"><circle cx="35" cy="24" r="5"/><path d="M28 54V36a7 7 0 0 1 14 0v18"/><line x1="40" y1="46" x2="50" y2="36"/></g></svg></div>
<div class="svc-label" style="left:922px;top:1727px">phlebotomy services</div>

<div class="btn" style="left:526px;top:1885px;width:148px;height:53px">View All</div>

<!-- TESTIMONIALS -->
<div class="eyebrow" style="top:2124px">Our Testimonials</div>
<h2 class="heading" style="top:2154px">What Our Client Say</h2>
<div class="abs" style="left:588px;top:2227px;width:1.5px;height:317px;background:#d5d5dc"></div>

<div class="avatar" style="left:298px;top:2248px;background:linear-gradient(180deg,#8c8f96,#2aa7c4)" role="img" aria-label="Portrait of a smiling young man"></div>
<p class="quote" style="left:152px;top:2368px">Lorem ipsum dolor sit amet, consectetur adipiscing elit, sed do eiusmod tempor incididunt ut labore et dolore magna aliqua. Ut enim ad minim veniam, quis nostrud exercitation ullamco laboris nisi ut aliquip .</p>
<div class="person" style="left:152px;top:2481px">Aria Velden</div>

<div class="avatar" style="left:794px;top:2248px;background:linear-gradient(180deg,#a65e48,#c7313a)" role="img" aria-label="Portrait of a smiling young woman"></div>
<p class="quote" style="left:649px;top:2368px">Lorem ipsum dolor sit amet, consectetur adipiscing elit, sed do eiusmod tempor incididunt ut labore et dolore magna aliqua. Ut enim ad minim veniam, quis nostrud exercitation ullamco laboris nisi ut aliquip .</p>
<div class="person" style="left:649px;top:2481px">Aria Velden</div>

<svg class="abs" style="left:586px;top:2557px" width="30" height="10"><circle cx="4" cy="5" r="3.5" fill="var(--teal)"/><circle cx="13" cy="5" r="3" fill="#ccd"/><circle cx="22" cy="5" r="3" fill="#ccd"/></svg>

<!-- BLOG -->
<section class="blog"></section>
<div class="eyebrow" style="top:2754px">Blog Posts</div>
<h2 class="heading" style="top:2783px">Our Latest News</h2>

<article class="card" style="left:122px">
  <div class="card-img" style="background:linear-gradient(135deg,#e9b9a8,#d84f8a 55%,#1f4e9c)" role="img" aria-label="Nurse applying a bandage to a patient's arm"></div>
  <div class="card-meta"><span>BY ADMIN</span><span>July 31, 2020</span><span>7 COMMENTS</span></div>
  <h3 class="card-title">Lorem ipsum dolor sit amet co sectetur adipiscing elit</h3>
  <p class="card-body">Lorem ipsum dolor sit amet, conse ctetur adipisicing elit. Accusamus fugiat at vitae, ratione.</p>
</article>
<article class="card" style="left:445px">
  <div class="card-img" style="background:linear-gradient(135deg,#c5ccd6,#eef0f3 50%,#7c8694)" role="img" aria-label="Scientists working at microscopes in a laboratory"></div>
  <div class="card-meta"><span>BY ADMIN</span><span>July 31, 2020</span><span>7 COMMENTS</span></div>
  <h3 class="card-title">Lorem ipsum dolor sit amet co sectetur adipiscing elit</h3>
  <p class="card-body">Lorem ipsum dolor sit amet, conse ctetur adipisicing elit. Accusamus fugiat at vitae, ratione.</p>
</article>
<article class="card" style="left:770px">
  <div class="card-img" style="background:linear-gradient(135deg,#5da7d8,#8fb8dd 45%,#a25a44)" role="img" aria-label="Gloved hands drawing blood from an arm"></div>
  <div class="card-meta"><span>BY ADMIN</span><span>July 31, 2020</span><span>7 COMMENTS</span></div>
  <h3 class="card-title">Lorem ipsum dolor sit amet co sectetur adipiscing elit</h3>
  <p class="card-body">Lorem ipsum dolor sit amet, conse ctetur adipisicing elit. Accusamus fugiat at vitae, ratione.</p>
</article>

<!-- CONTACT -->
<div class="ph" style="left:0;top:3314px;width:1200px;height:684px;background:radial-gradient(ellipse at 85% 40%,var(--lav-soft),transparent 55%)" role="img" aria-label="Faint molecular and DNA helix pattern"></div>
<div class="eyebrow" style="top:3407px">get in touch</div>
<h2 class="heading" style="top:3437px">Contact With Us</h2>
<form>
  <div class="field" style="left:222px;top:3513px;width:343px"><span>Full Name</span></div>
  <div class="field" style="left:631px;top:3513px;width:346px"><span>E-mail Address</span></div>
  <div class="field" style="left:222px;top:3640px;width:343px"><span>Phone Number</span></div>
  <div class="field" style="left:631px;top:3640px;width:346px"><span>Address</span></div>
  <div class="field" style="left:222px;top:3765px;width:755px"><span>Message</span></div>
  <div class="btn" style="left:526px;top:3849px;width:148px;height:53px">Submit</div>
</form>

<!-- FOOTER -->
<footer class="footer">
  <div class="brand" style="left:110px;top:82px">
    <div class="brand-mark"></div>
    <div>
      <div class="brand-name">Lumora</div>
      <div class="brand-sub">intravenous<br>medical clinic</div>
    </div>
  </div>
  <p class="f-text" style="left:113px;top:140px;width:290px">Lorem ipsum dolor sit amet, consectetur adipiscing elit, sed do eiusmod tempor incididunt ut labore et dolore magna aliqua. Ut enim ad minim .</p>

  <div class="f-head" style="left:479px">QUICK LINKS</div>
  <ul class="f-list" style="left:479px;top:112px">
    <li>» Home</li><li>» About Us</li><li>» Services</li><li>» Blog</li><li>» Contact Us</li>
  </ul>

  <div class="f-head" style="left:689px">CONTACT INFO</div>
  <svg class="abs" style="left:689px;top:118px" width="12" height="14" viewBox="0 0 12 14"><path d="M6 13s5-5 5-8a5 5 0 0 0-10 0c0 3 5 8 5 8z" fill="#fff"/><circle cx="6" cy="5" r="1.8" fill="var(--navy)"/></svg>
  <p class="f-text" style="left:713px;top:110px;width:210px">Lorem ipsum dolor sit am et, consectetur adip</p>
  <svg class="abs" style="left:689px;top:183px" width="12" height="12" viewBox="0 0 12 12"><path d="M2 1h3l1 3-2 1a7 7 0 0 0 3 3l1-2 3 1v3c-6 0-9-3-9-9z" fill="#fff"/></svg>
  <p class="f-text" style="left:713px;top:176px">+ 1 555 014 2290</p>
  <svg class="abs" style="left:689px;top:230px" width="13" height="10" viewBox="0 0 13 10"><rect width="13" height="10" rx="1" fill="#fff"/><path d="M0 1l6.5 5L13 1" fill="none" stroke="var(--navy)" stroke-width="1.2"/></svg>
  <p class="f-text" style="left:713px;top:222px">hello@lumoraclinic.net</p>

  <div class="f-head" style="left:955px">FOLLOW US ON</div>
  <div class="social" style="left:955px;top:115px"><i></i>Chatterly</div>
  <div class="social" style="left:955px;top:159px"><i></i>Snapfold</div>
</footer>
<div class="copy">© Copyrights 2020&nbsp; Lumora&nbsp; |&nbsp; All Rights Reserved</div>

</body>
</html>
```